Start-Up für Training, Coaching & Consulting sucht modernes Webdesign!
Zielgruppe
Wer ist TAVI Training, Coaching & Consulting?
Wir führen Führungskräftetrainings durch, machen Privatkunden für Bewerbungen fit und unterstützen Unternehmen mit Verkaufstrainings. Wir entwickeln Persönlichkeiten im Coaching. Wir beraten Unternehmen und helfen ihnen dabei, ihre Geschäftsabläufe und Prozesse zu optimieren. Dabei steht unsere hohe Qualität im Mittelpunkt - gemeinsam mit unseren kreativen Trainingsmethoden. Unser Background (Diplom-Kaufleute und geprüfte Trainer) bietet dafür die passende Ausgangslage.
Was bedeutet TAVI?
Tavi ist Maori und bdeutet Kreis/Spirale. Er symbolisiert einen wachsenden Silberfarn und steht für persönliche Entwicklung und Entfaltung. Der Tavi ist einerseits unser Namensgeber und unser Logo, andererseits steht der Tavi aber auch für unsere Werte: Denn wir wollen unseren Kunden dabei helfen zu wachsen und sich weiterzuentwickeln - und dies auf eine hochqualitative und seriöse Art und Weise ohne den Eindruck von Esoterik oder Erlebnispädagogik zu vermitteln.
Aufgabenstellung
Modernes Design, das unsere Philosophie widerspiegelt: Wir möchten unseren Kunden auf seriöse und hochqualitative Weise weiterentwickeln. Wir stehen für nachhaltigen Lernerfolg, kreative Trainingsmethoden, Abwechslung, Spaß am Lernen, Qualität, Kompetenz, Fachwissen und Dynamik.
Layout:
1) Header: QMSR geprüfter Trainer, Menüpunkte (siehe Architektur)
2) Banner
3) 3 Teaser (Training, Coaching, Consulting) + Header + 2-3 Zeilen Text (+Icons)
>>> Sichtbarer Bereich auf Homepage: Menü, Banner, Teaser
4) "Warum Sie uns wählen sollten": 5 bullet points ohne weiteren Text
5) "Aus unserem Blog": Frame für 3 Blogartikel + Bild + Datum + Header + 2-3 Zeilen Text
6) Alle drei QMSR Logos
7) Footer: Click Us (quick links), Contact Us (Adresse), Follow Us (Pinnwald, ZOLP, Kontaktor)
8) Copyright + Impressum
>>> Das Design soll klar sein, aber nicht zu kantig. Vielmehr sollen abgerundete Ecken und dynamische Elemente genutzt werden.
Architektur:
3 Ebenen:
1) Homepage
2) TAVI, Training, Coaching, Consulting, für Trainer, Kundenstimmen/Referenzen, Kontakt
3) noch zu bestimmende Produktdetailseiten
Texte werden noch erstellt, Layout kann ggf. mit Platzhaltertext gefüllt werden.
Bildmaterial: Logo und vorhandenes Imagebild werden zur Verfügung gestellt. Bilder können ggf. gekauft werden. Vorschläge erwünscht.
Corporate colors:
grün: #a2c61b + monochromatic colors
http://www.tintoskop.de/a2c61b
grau: #474747 + monochromatic colors
http://www.tintoskop.de/474747

```html
<!DOCTYPE html>
<html lang="de">
<head>
<meta charset="utf-8">
<title>TAVI Training, Coaching &amp; Consulting</title>
<link rel="stylesheet" href="https://fonts.googleapis.com/css2?family=Mulish:wght@300;400;600;700;800&display=swap">
<style>
:root{
  --lime:#a2c61b;
  --lime-bright:#c6e32c;
  --lime-pale:#e4eccd;
  --grey:#474747;
  --ink:#2f2f2f;
  --paper:#f1f1ef;
  --footer:#2a2d31;
  --footer-text:#b9bcbf;
  --nav-bg:rgba(28,36,26,.72);
  --badge:#1f5fa8;
}
*{box-sizing:border-box;margin:0;padding:0}
html,body{width:795px;height:1200px;overflow:hidden}
body{position:relative;background:var(--paper);font-family:"Mulish",sans-serif;color:var(--ink)}
.abs{position:absolute}
.hero-art{position:absolute;left:0;top:0}
.topbar{position:absolute;left:0;top:0;width:795px;height:53px;background:var(--nav-bg)}
.brand{position:absolute;left:112px;top:12px;display:flex;align-items:center;gap:5px;color:#fff;font-weight:800;font-size:22px;letter-spacing:.5px}
.brand-dot{width:12px;height:12px;border-radius:50%;background:var(--lime)}
.badge{position:absolute;left:201px;top:19px;width:66px;height:18px;background:var(--badge)}
.nav{position:absolute;top:0;left:302px;height:53px;display:flex;align-items:center;font-size:9px;color:#fff;text-transform:uppercase}
.nav a{color:inherit;text-decoration:none}
.nav .active{background:#1f2420;color:var(--lime);height:53px;display:flex;align-items:center;padding:0 9px;border-bottom:2px solid var(--lime)}
.nav .sep{margin:0 10px}
.nav .caret{color:var(--lime);font-size:8px;margin-left:3px}
.hero-title{position:absolute;left:0;width:795px;top:118px;text-align:center;color:#fff;font-weight:300;font-size:31px;line-height:35px}
.hero-title b{font-weight:800}
.hero-sub{position:absolute;left:0;width:795px;top:187px;text-align:center;color:#fff;font-size:13px;font-weight:400}
.hero-btn{position:absolute;left:347px;top:215px;width:99px;height:33px;border-radius:17px;background:var(--lime);color:#fff;font-size:8.5px;font-weight:700;display:flex;align-items:center;justify-content:center}
.arrow{position:absolute;top:148px}
.teaser{position:absolute;top:342px;width:150px;text-align:center}
.teaser .ring{width:150px;height:150px;border-radius:50%;background:var(--lime-pale);padding:11px}
.teaser .photo{width:128px;height:128px;border-radius:50%}
.teaser h3{margin-top:13px;font-size:9.5px;font-weight:600;letter-spacing:.2px}
.teaser .rule{border-top:1px dotted #9a9a9a;margin:8px 4px 5px}
.teaser p{font-size:7.3px;line-height:10.5px;font-weight:300}
.divider{position:absolute;left:80px;width:635px;height:1px;background:#d4d6cc}
.divider-mark{position:absolute;width:26px;height:26px;border-radius:50%;background:var(--lime-pale);border:5px solid #d8e89a}
.sec-title{position:absolute;font-size:17px;font-weight:400;color:var(--ink)}
.sec-rule{position:absolute;height:1px;border-top:1px dotted #8a8a8a}
.why{position:absolute;left:118px;top:662px;list-style:none}
.why li{display:flex;align-items:center;height:29.6px;font-size:13px;font-weight:300}
.why .tick{width:14px;height:14px;border-radius:50%;background:var(--lime);margin-right:8px;display:flex;align-items:center;justify-content:center}
.post{position:absolute;left:463px;width:202px}
.post .thumb{position:absolute;left:0;top:0;width:46px;height:46px;border-radius:50%;border:3px solid var(--lime-pale)}
.post .body{position:absolute;left:58px;top:0;width:150px}
.post .date{font-size:7.3px;color:var(--lime);line-height:10px}
.post p{font-size:7.3px;line-height:10.6px;font-weight:300}
.post .more{display:inline-block;margin-top:3px;width:38px;height:12px;border-radius:6px;background:var(--lime);color:#fff;font-size:6.5px;text-align:center;line-height:12px}
.post-rule{position:absolute;left:465px;width:198px;border-top:1px dotted #9ab035}
.partner{position:absolute;background:var(--badge)}
.footer-art{position:absolute;left:0;top:880px}
.foot-brand{position:absolute;left:118px;top:1011px;display:flex;align-items:center;gap:4px;color:#fff;font-weight:800;font-size:16px}
.foot-brand .brand-dot{width:9px;height:9px}
.foot-links{position:absolute;left:117px;top:1044px;list-style:none;font-size:8.3px;color:var(--footer-text)}
.foot-links li{height:16px}
.contact{position:absolute;top:1044px}
.contact h4{font-size:8.5px;font-weight:400;color:var(--lime);margin-bottom:3px}
.contact p{font-size:6.8px;line-height:12.7px;color:var(--footer-text);font-weight:300}
.contact .ico{position:absolute;left:-26px;top:0}
.follow{position:absolute;left:604px;top:1044px;font-size:8.5px;color:var(--footer-text)}
.socials{position:absolute;left:596px;top:1061px;display:flex;gap:6px}
.socials span{width:23px;height:23px;border-radius:50%;background:var(--lime)}
.foot-rule{position:absolute;left:117px;top:1134px;width:560px;border-top:1px dotted var(--lime)}
.copy{position:absolute;left:0;top:1151px;width:795px;text-align:center;font-size:8px;line-height:13px;color:var(--footer-text);font-weight:300}
</style>
</head>
<body>

<svg class="hero-art" width="795" height="340" viewBox="0 0 795 340" role="img" aria-label="Hero photo: unfolding green fern fronds on a soft green background">
  <defs>
    <radialGradient id="fern" cx="50%" cy="40%" r="70%">
      <stop offset="0" stop-color="#3f8a1e"/>
      <stop offset=".6" stop-color="#2d6a14"/>
      <stop offset="1" stop-color="#1d4a0d"/>
    </radialGradient>
  </defs>
  <path d="M0 0H795V205C700 270 560 305 420 300C280 295 120 265 0 265Z" fill="url(#fern)"/>
  <path d="M0 265C120 265 280 295 420 300C560 305 700 270 795 205V235C700 300 560 330 420 328C260 326 120 290 0 290Z" fill="var(--lime)"/>
  <path d="M0 265C120 265 280 295 420 300C560 305 700 270 795 205V214C700 282 560 312 420 309C270 305 120 276 0 276Z" fill="var(--lime-bright)" opacity=".7"/>
</svg>

<header class="topbar">
  <div class="brand"><span>TAVI</span><span class="brand-dot"></span></div>
  <div class="badge" role="img" aria-label="QMSR certified trainer badge"></div>
  <nav class="nav">
    <a class="active" href="#">Home</a><span class="sep">|</span>
    <a href="#">Über uns<span class="caret">&#10095;</span></a><span class="sep">|</span>
    <a href="#">Für Trainers<span class="caret">&#10095;</span></a><span class="sep">|</span>
    <a href="#">Referenzen</a><span class="sep" style="margin:0 18px">|</span>
    <a href="#">Kontakt</a>
  </nav>
</header>

<svg class="arrow" style="left:48px" width="28" height="44" viewBox="0 0 28 44"><path d="M24 4L6 22L24 40" fill="none" stroke="rgba(255,255,255,.55)" stroke-width="6" stroke-linecap="round"/></svg>
<svg class="arrow" style="left:719px" width="28" height="44" viewBox="0 0 28 44"><path d="M4 4L22 22L4 40" fill="none" stroke="rgba(255,255,255,.55)" stroke-width="6" stroke-linecap="round"/></svg>

<h1 class="hero-title">TRAINING, COACHING<br>CONSULTING <b>FÜR TRAINER</b></h1>
<p class="hero-sub">Lorem ipsum dolor sit amet consectetur adipiscing elit.</p>
<div class="hero-btn">MEHR ERFAHREN</div>

<section>
  <div class="teaser" style="left:135px">
    <div class="ring"><div class="photo" role="img" aria-label="Photo: folded hands resting on a notebook on a desk" style="background:radial-gradient(circle at 50% 40%,#c9d9ea,#6f8fb3 70%,#3b4c66)"></div></div>
    <h3>LOREM IPSUM DOLOR SIT</h3><div class="rule"></div>
    <p>Lorem ipsum dolor sit amet, consectetur adipiscing elit. In dapibus accumsan luctus.</p>
  </div>
  <div class="teaser" style="left:322px">
    <div class="ring"><div class="photo" role="img" aria-label="Photo: two colleagues in business attire looking at a tablet" style="background:radial-gradient(circle at 50% 40%,#e8e6e2,#9a9590 70%,#3a3a3e)"></div></div>
    <h3>ADIPISCING ELIT</h3><div class="rule"></div>
    <p>Dolor sit amet, consectetur adipiscing elit. In dapibus accumsan luctus.</p>
  </div>
  <div class="teaser" style="left:506px">
    <div class="ring"><div class="photo" role="img" aria-label="Photo: hands working on a tablet with a stylus" style="background:radial-gradient(circle at 50% 40%,#eef1f3,#a9b5bd 70%,#5b6770)"></div></div>
    <h3>ELIT NON VEHICULA</h3><div class="rule"></div>
    <p>Sit amet, consectetur adipiscing elit. In dapibus accumsan luctus.</p>
  </div>
</section>

<div class="divider" style="top:583px"></div>
<div class="divider-mark" style="left:384px;top:570px"></div>

<svg class="abs" style="left:0;top:770px" width="400" height="90" viewBox="0 0 400 90"><path d="M0 55C120 70 260 90 330 60C380 40 397 10 397 0V40C390 70 340 90 250 88C160 86 60 70 0 60Z" fill="#e6efc6" opacity=".7"/></svg>

<h2 class="sec-title" style="left:139px;top:620px">WHY CHOOSE US</h2>
<div class="sec-rule" style="left:139px;top:648px;width:142px"></div>
<ul class="why">
  <li><span class="tick"><svg width="6" height="7" viewBox="0 0 6 7"><path d="M1.5 1L4.5 3.5L1.5 6" fill="none" stroke="#fff" stroke-width="1.4"/></svg></span>Vestibulum nec mauris facilisis</li>
  <li><span class="tick"><svg width="6" height="7" viewBox="0 0 6 7"><path d="M1.5 1L4.5 3.5L1.5 6" fill="none" stroke="#fff" stroke-width="1.4"/></svg></span>Curabitur et tristique diam, nec sagittis nibh</li>
  <li><span class="tick"><svg width="6" height="7" viewBox="0 0 6 7"><path d="M1.5 1L4.5 3.5L1.5 6" fill="none" stroke="#fff" stroke-width="1.4"/></svg></span>Denim nec sagittis nibh</li>
  <li><span class="tick"><svg width="6" height="7" viewBox="0 0 6 7"><path d="M1.5 1L4.5 3.5L1.5 6" fill="none" stroke="#fff" stroke-width="1.4"/></svg></span>Vestibulum nec mauris facilisis</li>
  <li><span class="tick"><svg width="6" height="7" viewBox="0 0 6 7"><path d="M1.5 1L4.5 3.5L1.5 6" fill="none" stroke="#fff" stroke-width="1.4"/></svg></span>Tristique diam nec lorem</li>
</ul>

<h2 class="sec-title" style="left:469px;top:620px">BLOG</h2>
<div class="sec-rule" style="left:469px;top:648px;width:45px"></div>

<article class="post" style="top:664px">
  <div class="thumb" role="img" aria-label="Blog photo: two colleagues in business attire" style="background:radial-gradient(circle,#d9d6d0,#6e6a66)"></div>
  <div class="body">
    <div class="date">08.12.2015 Sit Amet Adipiscing</div>
    <p>Lorem ipsum dolor sit amet, consectetur adipiscing elit. In dapibus accumsan luctus. Aliquam posuere eros sed nibh sagittis,</p>
    <span class="more">more</span>
  </div>
</article>
<div class="post-rule" style="top:722px"></div>
<article class="post" style="top:731px">
  <div class="thumb" role="img" aria-label="Blog photo: businessman with glasses" style="background:radial-gradient(circle,#e2e0dc,#7a7672)"></div>
  <div class="body">
    <div class="date">08.12.2015 Lorem Ipsum Dolor</div>
    <p>Pellentesque habitant morbi tristique senectus et netus et malesuada fames ac turpis egestas.</p>
    <span class="more">more</span>
  </div>
</article>
<div class="post-rule" style="top:791px"></div>
<article class="post" style="top:799px">
  <div class="thumb" role="img" aria-label="Blog photo: hands using a tablet" style="background:radial-gradient(circle,#eef1f3,#8e9aa3)"></div>
  <div class="body">
    <div class="date">08.12.2015 Adipiscing Vehicula</div>
    <p>Mauris sollicitudin felis aliquam ipsum dictum vehicula. Donec feugiat sapien nunc, quis auctor libero finibus in.</p>
    <span class="more">more</span>
  </div>
</article>

<div class="divider" style="top:885px;background:#cfe08a"></div>
<div class="divider-mark" style="left:384px;top:872px"></div>

<svg class="footer-art" width="795" height="320" viewBox="0 0 795 320">
  <path d="M0 65C200 75 350 110 450 108C600 104 720 60 795 10V320H0Z" fill="var(--lime)"/>
  <path d="M0 65C200 75 350 110 450 108C600 104 720 60 795 10V22C720 72 600 114 450 117C350 119 200 86 0 76Z" fill="var(--lime-bright)"/>
  <path d="M0 88C200 100 350 128 450 126C600 122 720 90 795 50V320H0Z" fill="var(--footer)"/>
</svg>

<div class="partner" style="left:273px;top:937px;width:66px;height:18px" role="img" aria-label="QMSR certified business trainer badge"></div>
<div class="partner" style="left:368px;top:930px;width:24px;height:30px" role="img" aria-label="QMSR member badge"></div>
<div class="partner" style="left:448px;top:930px;width:24px;height:30px" role="img" aria-label="QMSR association badge"></div>

<div class="foot-brand"><span>TAVI</span><span class="brand-dot"></span></div>
<ul class="foot-links">
  <li>HOME</li><li>ÜBER UNS</li><li>FÜR TRAINERS</li><li>REFERENZEN</li><li>KONTAKT</li>
</ul>

<div class="contact" style="left:230px">
  <svg class="ico" width="14" height="12" viewBox="0 0 14 12"><path d="M7 0L0 6H2V12H5.5V8H8.5V12H12V6H14Z" fill="var(--lime)"/></svg>
  <h4>Address</h4>
  <p>Vestibulum nec mauris 62<br>Suscipit est et<br>62134 Townname</p>
</div>
<div class="contact" style="left:361px">
  <svg class="ico" width="12" height="12" viewBox="0 0 12 12"><rect width="12" height="12" rx="2.5" fill="var(--lime)"/><path d="M3.5 2.5L5 4.5L4.3 5.5C4.8 6.6 5.6 7.3 6.6 7.8L7.6 7.1L9.5 8.5L8.6 9.6C6 9.4 2.9 6.4 2.5 3.4Z" fill="var(--footer)"/></svg>
  <h4>Phone</h4>
  <p>(000 &nbsp;123 &nbsp;7658 903<br>(000 &nbsp;123 &nbsp;7658 903<br>(000 &nbsp;123 &nbsp;7658 903</p>
</div>
<div class="contact" style="left:481px">
  <svg class="ico" width="13" height="10" viewBox="0 0 13 10"><rect width="13" height="10" rx="1" fill="var(--lime)"/><path d="M0.5 1L6.5 5.5L12.5 1" fill="none" stroke="var(--footer)" stroke-width="1.2"/></svg>
  <h4>Email</h4>
  <p>info@tavi.com<br>addressinfo@tavi.com<br>emailadd@tavi.com</p>
</div>

<div class="follow">BITTE FOLGEN</div>
<div class="socials">
  <span role="img" aria-label="Pinnwald"></span>
  <span role="img" aria-label="Zwitscherl"></span>
  <span role="img" aria-label="Kontaktor"></span>
</div>

<div class="foot-rule"></div>
<p class="copy">Aliquam at pulvinar mi. Nulla eget bibendum nisl. Integer consectetur quam ac purus pharetra pulvinar.<br>Aenean faucibus tortor ac tortor aliquet tincidunt. Mauris eget maximus urna.</p>

</body>
</html>
```